New Business Card Design Project

We require a business card design for Vexalund, a newly established Indian company.
Our focus is on the development, manufacturing, and export of a diverse array of pharmaceutical products on a global scale. The card should convey a professional appearance, as our primary markets are in Africa, China, and Southeast Asian nations.
We envision a two-sided business card, with the reverse side dedicated to a logo set against a solid color or an elegantly designed pattern. The corners should be rounded. We would appreciate seeing both horizontal and vertical design options. We trust the designer to utilize their expertise in creating this design.

The content for the business card is included in the attached Word file.

Target Market(s)

Our primary markets are in Africa, China, and Southeast Asian, Latin America, Maldives, Sri Lanka

Industry/Entity Type

Pharmaceutical Manufacturing and Export

Contact Information for Business Card

Colors

Designer to choose colors to be used in the design.

Requirements
Must have
• The reverse side of the business card features solely the logo along with the tagline, "Care Beyond Borders."
Should not have
• The logo should not exceed two instances, encompassing both the front and back sides of the card.

```html
<!DOCTYPE html>
<html lang="en">
<head>
<meta charset="utf-8">
<title>Vexalund Business Card</title>
<link href="https://fonts.googleapis.com/css2?family=Montserrat:wght@500;800&family=Open+Sans:wght@400;600&display=swap" rel="stylesheet">
<style>
  :root {
    --stage: #232325;
    --card: #1e1e21;
    --edge: #2ba3dc;
    --blue: #2ea6e0;
    --coral: #ef6550;
    --white: #f2f2f2;
    --soft: #d9d9d9;
  }
  * { box-sizing: border-box; margin: 0; padding: 0; }
  html, body {
    width: 1200px; height: 711px; overflow: hidden;
    background: var(--stage);
  }
  .stage {
    position: relative; width: 1200px; height: 711px;
    display: flex; align-items: center; justify-content: center; gap: 50px;
  }
  .card {
    position: relative; width: 530px; height: 303px;
    background: var(--card);
    border-radius: 22px;
    border-bottom: 3px solid var(--edge);
    border-left: 2px solid var(--edge);
    box-shadow: 0 18px 30px rgba(0,0,0,.55);
    overflow: hidden;
  }
  .wordmark {
    font-family: "Montserrat", sans-serif;
    font-weight: 800;
    color: var(--blue);
    letter-spacing: .5px;
    line-height: 1;
    display: flex; align-items: center; gap: 10px;
  }
  .wordmark .dot {
    width: 14px; height: 14px; border-radius: 50%;
    background: var(--coral);
  }
  /* back side */
  .card-back {
    display: flex; flex-direction: column; align-items: center; justify-content: center;
  }
  .card-back .wordmark { font-size: 54px; }
  .tagline {
    margin-top: 16px;
    font-family: "Montserrat", sans-serif; font-weight: 500;
    font-size: 13px; color: var(--white); letter-spacing: .5px;
  }
  /* front side */
  .accent-bar {
    position: absolute; top: 14px; right: 0;
    width: 14px; height: 44px; background: var(--blue);
  }
  .holder {
    position: absolute; top: 22px; right: 30px; text-align: right;
  }
  .holder-name {
    font-family: "Montserrat", sans-serif; font-size: 22px; line-height: 1;
  }
  .holder-name .first { color: var(--blue); font-weight: 800; }
  .holder-name .rest { color: var(--coral); font-weight: 500; }
  .holder-role {
    margin-top: 4px;
    font-family: "Open Sans", sans-serif; font-size: 11px; color: var(--white);
  }
  .company { position: absolute; left: 34px; top: 108px; }
  .company .wordmark { font-size: 38px; }
  .address {
    margin-top: 16px;
    font-family: "Open Sans", sans-serif; font-size: 11.5px; line-height: 1.45;
    color: var(--soft);
  }
  .contacts {
    position: absolute; left: 34px; bottom: 22px;
    list-style: none;
    font-family: "Open Sans", sans-serif; font-size: 12px; color: var(--white);
  }
  .contacts li { display: flex; align-items: center; gap: 9px; margin-top: 5px; }
  .contacts svg { width: 14px; height: 14px; flex: none; }
</style>
</head>
<body>
<main class="stage">
  <section class="card card-back" aria-label="Card reverse">
    <div class="wordmark"><span class="dot"></span>Vexalund</div>
    <p class="tagline">Care Beyond Borders.</p>
  </section>

  <section class="card card-front" aria-label="Card front">
    <span class="accent-bar"></span>
    <div class="holder">
      <p class="holder-name"><span class="first">Rohan</span> <span class="rest">K. Selvar</span></p>
      <p class="holder-role">CEO</p>
    </div>
    <div class="company">
      <div class="wordmark"><span class="dot"></span>Vexalund</div>
      <p class="address">14, Neelgiri Colony,<br>Aranpur, 410233, India</p>
    </div>
    <ul class="contacts">
      <li>
        <svg viewBox="0 0 14 14" aria-hidden="true"><rect x="3" y="1" width="8" height="12" rx="1.5" fill="none" stroke="#ef6550" stroke-width="1.4"/></svg>
        +919 400173582
      </li>
      <li>
        <svg viewBox="0 0 14 14" aria-hidden="true"><circle cx="7" cy="7" r="6" fill="none" stroke="#2ea6e0" stroke-width="1.3"/><ellipse cx="7" cy="7" rx="2.6" ry="6" fill="none" stroke="#2ea6e0" stroke-width="1"/><line x1="1" y1="7" x2="13" y2="7" stroke="#2ea6e0" stroke-width="1"/></svg>
        www.vexalund.com
      </li>
      <li>
        <svg viewBox="0 0 14 14" aria-hidden="true"><rect x="1" y="3" width="12" height="9" rx="1" fill="#ef6550"/><polyline points="1.5,3.5 7,8 12.5,3.5" fill="none" stroke="#1e1e21" stroke-width="1.2"/></svg>
        rselvar@vexalund.com
      </li>
    </ul>
  </section>
</main>
</body>
</html>
```